Beacon Advisory Website

I currently have a website www.beaconadvisoryinc.com. We are a IT Consulting Company. Our website will pretty much tell out our services. I am looking to enhance my website and make it look more professional. Looking for very classy and Contemporary look and design for my website.

It Company

```html
<!DOCTYPE html>
<html lang="en">
<head>
<meta charset="utf-8">
<title>Beacon Advisory</title>
<link href="https://fonts.googleapis.com/css2?family=Lato:wght@300;400;700;900&family=Josefin+Sans:wght@300;400&display=swap" rel="stylesheet">
<style>
:root{
  --blue:#0a66a8;
  --blue-dark:#075a95;
  --ink:#1a1a1a;
  --text:#333;
  --topbar:#3b3b3b;
  --footer-bottom:#2f2f2f;
  --light:#f6f6f6;
  --news:#e4e4e4;
  --white:#fff;
}
*{margin:0;padding:0;box-sizing:border-box}
html,body{width:1015px;height:1200px;overflow:hidden}
body{position:relative;font-family:'Lato',sans-serif;color:var(--text);background:var(--white)}
.abs{position:absolute}
.topbar{left:0;top:0;width:1015px;height:24px;background:linear-gradient(#555,#2e2e2e);color:#fff;font-size:12px}
.topbar .item{position:absolute;top:4px;display:flex;align-items:center;gap:6px}
.topbar .sep{position:absolute;left:717px;top:2px;width:1px;height:20px;background:#777}
.header{left:0;top:24px;width:1015px;height:70px;background:#fff}
.brand{position:absolute;left:112px;top:22px;display:flex;align-items:center;gap:8px;color:var(--blue);font-weight:900;font-size:20px;letter-spacing:.5px}
.brand .dot{width:22px;height:22px;border-radius:50%;background:var(--blue)}
.nav{position:absolute;left:422px;top:0;height:70px;display:flex}
.nav a{display:flex;align-items:center;padding:0 10px;height:70px;font-size:13px;font-weight:700;color:#222;text-decoration:none;border-left:1px solid #e2e2e2}
.nav a:first-child{border-left:none}
.nav a.active{background:var(--blue);color:#fff}
.hero{left:0;top:94px;width:1015px;height:452px;background:linear-gradient(100deg,#5a5f66 0%,#8a8e93 35%,#a6a8aa 60%,#9c9ea0 100%)}
.hero-text{position:absolute;left:540px;top:154px;width:410px;text-align:center;font-family:'Josefin Sans',sans-serif;font-size:28px;line-height:41px;color:#fff;text-shadow:0 1px 3px rgba(0,0,0,.45)}
.dots{position:absolute;left:726px;top:294px;display:flex;gap:9px}
.dots span{width:14px;height:14px;border-radius:50%;background:#fff;border:2px solid #fff}
.dots span:first-child{background:transparent}
.band{left:0;top:546px;width:1015px;height:183px;background:var(--blue)}
.card{position:absolute;top:438px;width:224px;height:258px;background:#fff;border-radius:12px 12px 0 12px;box-shadow:0 6px 6px -2px rgba(0,0,0,.45);text-align:center;overflow:hidden}
.card .photo{height:120px;margin:3px 3px 0;border-radius:10px 10px 0 0}
.card .badge{width:36px;height:36px;border-radius:50%;background:var(--blue);border:3px solid #fff;margin:-19px auto 0;position:relative}
.card h3{margin-top:9px;font-size:15px;font-weight:900;color:#111;letter-spacing:.3px}
.card p{margin:9px 14px 0;font-size:11px;line-height:15.5px;color:#333}
.more{display:inline-block;font-size:11px;font-weight:700;color:var(--blue-dark);text-decoration:underline}
.card .more{margin-top:9px}
.welcome{left:0;top:729px;width:1015px;height:249px;background:var(--light);text-align:center}
.welcome h2{margin-top:42px;font-family:'Josefin Sans',sans-serif;font-weight:300;font-size:29px;color:#111;letter-spacing:.3px}
.welcome h2 b{font-family:'Lato',sans-serif;font-weight:900;color:var(--blue);font-size:27px}
.welcome p{width:780px;margin:10px auto 0;font-size:13px;line-height:23px;color:#222}
.welcome .more{margin-top:10px}
.footer{left:0;top:978px;width:1015px;height:180px;background:var(--blue);color:#fff}
.news{position:absolute;left:120px;top:-8px;width:242px;height:172px;background:var(--news);color:#222}
.news h4{position:absolute;left:12px;top:22px;font-weight:300;font-size:14px;letter-spacing:.3px}
.news .arrows{position:absolute;right:16px;top:22px;font-size:13px}
.news .rule{position:absolute;left:12px;top:44px;width:218px;height:1px;background:#bbb}
.news-item{position:absolute;left:12px;display:flex;gap:6px}
.date{width:39px;text-align:center}
.date .m{background:var(--blue);color:#fff;font-size:10px;height:16px;line-height:16px}
.date .d{background:#1f1f1f;color:#fff;font-size:14px;font-weight:700;height:22px;line-height:22px}
.news-item p{font-size:10.5px;line-height:14px;width:172px}
.fold{position:absolute;right:0;bottom:0;width:0;height:0;border-left:14px solid #bdbdbd;border-top:14px solid transparent}
.col{position:absolute;top:16px}
.col h4{font-weight:300;font-size:12.5px;letter-spacing:.5px;padding-bottom:6px;border-bottom:1px solid rgba(255,255,255,.6)}
.col ul{list-style:none;margin-top:9px}
.col li{font-size:11px;line-height:17.3px}
.vline{position:absolute;top:20px;width:1px;height:140px;background:rgba(255,255,255,.25)}
.input{margin-top:14px;width:175px;height:25px;background:#fff;border-radius:2px;color:#777;font-size:10px;padding:7px 10px}
.btn{margin-top:11px;width:96px;height:25px;background:#fff;border-radius:2px;color:var(--blue);font-weight:900;font-size:11px;text-align:center;line-height:25px}
.contact-row{display:flex;gap:8px;font-size:11px;line-height:14.5px;margin-top:4px}
.contact-row svg{flex:none;margin-top:2px}
.bottom{left:0;top:1158px;width:1015px;height:42px;background:var(--footer-bottom);color:#eee;font-size:12.5px}
.bottom .copy{position:absolute;left:112px;top:13px}
.social{position:absolute;left:797px;top:15px;display:flex;gap:18px}
.social span{width:13px;height:13px;border-radius:50%;background:#bdbdbd}
</style>
</head>
<body>

<div class="abs topbar">
  <div class="item" style="left:581px">
    <svg width="11" height="12" viewBox="0 0 24 24"><path fill="#fff" d="M6.6 10.8a15 15 0 0 0 6.6 6.6l2.2-2.2c.3-.3.7-.4 1-.2 1.1.4 2.3.6 3.6.6.6 0 1 .4 1 1V20c0 .6-.4 1-1 1A17 17 0 0 1 3 4c0-.6.4-1 1-1h3.5c.6 0 1 .4 1 1 0 1.3.2 2.5.6 3.6.1.3 0 .7-.2 1z"/></svg>
    +1 (555) 014 2290
  </div>
  <div class="sep"></div>
  <div class="item" style="left:731px">
    <svg width="14" height="10" viewBox="0 0 14 10"><rect width="14" height="10" fill="#fff"/><path d="M0 0l7 5 7-5" fill="none" stroke="#444" stroke-width="1.2"/></svg>
    hello@beaconadvisoryinc.com
  </div>
</div>

<div class="abs header">
  <div class="brand"><span class="dot"></span>BEACON ADVISORY</div>
  <nav class="nav">
    <a class="active">HOME</a><a>SERVICES</a><a>SOLUTIONS</a><a>RESOURCES</a><a>CAREER</a><a>CONTACT US</a>
  </nav>
</div>

<div class="abs hero" role="img" aria-label="Photo of two business professionals smiling while reviewing documents at an office desk">
  <div class="hero-text">We Understand The<br>Complexities Management<br>Faces When Staffing A Project.</div>
  <div class="dots"><span></span><span></span><span></span></div>
</div>

<div class="abs band"></div>

<div class="card" style="left:112px">
  <div class="photo" role="img" aria-label="Photo of hands working on a tablet at a desk" style="background:linear-gradient(135deg,#6d7f96,#c9d2dc)"></div>
  <div class="badge"></div>
  <h3>CONSULTING</h3>
  <p>Beacon Advisory has certified professional consultants to work with you to help increase the business ...</p>
  <a class="more">Read More »</a>
</div>
<div class="card" style="left:395px">
  <div class="photo" role="img" aria-label="Photo of business team silhouettes in front of bright office windows" style="background:linear-gradient(180deg,#e6e6e6,#3a3a3a)"></div>
  <div class="badge"></div>
  <h3>STAFF AUGMENTATION</h3>
  <p>For years Beacon Advisory as been offering our customers the ability to augment their existing staff ...</p>
  <a class="more">Read More »</a>
</div>
<div class="card" style="left:681px">
  <div class="photo" role="img" aria-label="Photo of colleagues reviewing charts on a meeting table" style="background:linear-gradient(135deg,#b9c7d8,#eef1f5)"></div>
  <div class="badge"></div>
  <h3>OFFSHORE</h3>
  <p>Our Offshore development model has a unique distinction of providing efficient software solutions ...</p>
  <a class="more">Read More »</a>
</div>

<section class="abs welcome">
  <h2>WELCOME TO <b>BEACON ADVISORY</b></h2>
  <p>Today's IT market is a dynamic, fast-paced industry, with ever-increasing demands. Meeting these demands for over 25 years, Beacon Advisory maintains a global presence, aggressively recruiting expertly qualified IT and Management Professionals from around the world and cultivating key partnerships with corporations to understand their business models end-to-end, with a goal of delivering exceptional client service and ensuring a consistent delivery of the talent needed to drive results.</p>
  <a class="more">Read More »</a>
</section>

<footer class="abs footer">
  <div class="news">
    <h4>LATEST NEWS</h4>
    <div class="arrows">‹&nbsp;&nbsp;›</div>
    <div class="rule"></div>
    <div class="news-item" style="top:58px">
      <div class="date"><div class="m">MAR</div><div class="d">01</div></div>
      <p>Lorem ipsum dolor sit amet, Lorem consectetuer adipiscing elit, sed</p>
    </div>
    <div class="news-item" style="top:110px">
      <div class="date"><div class="m">MAR</div><div class="d">01</div></div>
      <p>Lorem ipsum dolor sit amet, Lorem consectetuer adipiscing elit, sed</p>
    </div>
    <div class="fold"></div>
  </div>

  <div class="col" style="left:384px;width:82px">
    <h4>QUICK LINKS</h4>
    <ul><li>› Home</li><li>› Services</li><li>› Solutions</li><li>› Resources</li><li>› Career</li><li>› Contact Us</li></ul>
  </div>
  <div class="vline" style="left:486px"></div>

  <div class="col" style="left:513px;width:163px">
    <h4>NEWSLETTER</h4>
    <p style="font-size:10.5px;line-height:15px;margin-top:9px">Get Latest Updates By Entering Your Email Address</p>
    <div class="input">Email Address</div>
    <div class="btn">SUBSCRIBE</div>
  </div>
  <div class="vline" style="left:708px"></div>

  <div class="col" style="left:736px;width:162px">
    <h4>CONTACT DETAILS</h4>
    <div class="contact-row" style="margin-top:10px">
      <svg width="10" height="13" viewBox="0 0 10 13"><path fill="#fff" d="M5 0a5 5 0 0 1 5 5c0 3.5-5 8-5 8S0 8.5 0 5a5 5 0 0 1 5-5z"/><circle cx="5" cy="5" r="2" fill="#0a66a8"/></svg>
      <div><b>Beacon Advisory INC.</b><br>420 Harbor Lane<br>Suite 310<br>Riverton, NJ 08077</div>
    </div>
    <div class="contact-row" style="margin-top:5px">
      <svg width="11" height="11" viewBox="0 0 24 24"><path fill="#fff" d="M6.6 10.8a15 15 0 0 0 6.6 6.6l2.2-2.2c.3-.3.7-.4 1-.2 1.1.4 2.3.6 3.6.6.6 0 1 .4 1 1V20c0 .6-.4 1-1 1A17 17 0 0 1 3 4c0-.6.4-1 1-1h3.5c.6 0 1 .4 1 1 0 1.3.2 2.5.6 3.6.1.3 0 .7-.2 1z"/></svg>
      <div>+1 (555) 014 2290</div>
    </div>
    <div class="contact-row" style="margin-top:6px">
      <svg width="11" height="9" viewBox="0 0 14 10"><rect width="14" height="10" fill="#fff"/><path d="M0 0l7 5 7-5" fill="none" stroke="#0a66a8" stroke-width="1.2"/></svg>
      <div>hello@beaconadvisoryinc.com</div>
    </div>
  </div>
</footer>

<div class="abs bottom">
  <div class="copy">© 2016 - Beacon Advisory INC.&nbsp;&nbsp;|&nbsp;&nbsp;All Rights Reserved</div>
  <div class="social"><span></span><span></span><span></span><span></span></div>
</div>

</body>
</html>
```